We need our current web site completely overhauled logo and all. www.maplecrestkidsclub.com

This is a web site for a before and after school program for kids. I would like to see a fresh and cleaner version. The current version was created 8 to 10 years ago.
www.maplecrestkidsclub.com

```html
<!DOCTYPE html>
<html lang="en">
<head>
<meta charset="utf-8">
<title>Maplecrest Kids Club</title>
<link rel="stylesheet" href="https://fonts.googleapis.com/css2?family=PT+Sans:wght@400;700&display=swap">
<style>
:root{
  --green:#2f8a0c;
  --green-dark:#3f7f0e;
  --green-light:#6cb81f;
  --orange:#f0a000;
  --orange-light:#ffc21a;
  --text:#555;
  --line:#d9d9d9;
  --grey-circle:#7d7d7d;
  --caption:rgba(20,20,20,.78);
}
*{box-sizing:border-box;margin:0;padding:0}
html,body{width:1070px;height:1200px;overflow:hidden;background:#fff}
body{position:relative;font-family:"PT Sans",sans-serif;color:var(--text)}
.abs{position:absolute}
a{color:inherit;text-decoration:none}

.brand{left:162px;top:34px;display:flex;align-items:center;gap:8px;font-size:22px;font-weight:700;color:var(--green-dark)}
.brand-dot{width:26px;height:26px;border-radius:50%;background:var(--green-dark)}

.top-nav{right:160px;top:31px;display:flex;font-size:8.5px;color:#444;text-transform:uppercase}
.top-nav a{padding:0 13px;border-left:1px solid #444;line-height:10px}
.top-nav a:first-child{border-left:none}
.top-nav a:last-child{padding-right:0}

.btn{display:flex;align-items:center;justify-content:center;color:#fff;border-radius:2px;
  background:linear-gradient(#ffc21a,#f09400);box-shadow:0 1px 2px rgba(0,0,0,.25)}
.newsletter{left:757px;top:60px;width:153px;height:30px;font-size:11px;gap:6px}
.read-more{width:80px;height:24px;font-size:10px}

.main-nav{left:161px;top:110px;width:749px;height:37px;border-radius:3px;
  background:linear-gradient(#6cb81f,#2f8a0c);display:flex;justify-content:space-between;align-items:center;padding:0 30px;
  box-shadow:0 2px 2px rgba(0,0,0,.2)}
.main-nav a{color:#fff;font-size:9.5px;font-weight:700;text-transform:uppercase}

.hero{left:161px;top:158px;width:749px;height:329px;
  background:linear-gradient(120deg,#5bb6c9 0%,#9fcad4 30%,#e7c8a4 55%,#d99c6c 75%,#c77f4f 100%)}
.hero-shadow{left:200px;top:487px;width:670px;height:16px;background:radial-gradient(ellipse at top,rgba(0,0,0,.15),transparent 70%)}
.caption{background:var(--caption);color:#fff;font-size:17px;font-weight:700;text-transform:uppercase;display:flex;align-items:center;padding-left:20px}
.caption-title{left:161px;top:389px;width:171px;height:37px}
.caption-sub{left:161px;top:432px;width:553px;height:37px}
.slider-arrows{left:861px;top:460px;width:38px;height:15px;background:rgba(0,0,0,.15);display:flex;justify-content:space-around;align-items:center;color:#fff;font-size:9px}

h2{color:var(--green);font-size:14px;font-weight:700;text-transform:uppercase}
.body-text{font-size:8.5px;line-height:16px}

.welcome-title{left:162px;top:523px}
.welcome-text{left:162px;top:547px;width:748px}

.card{top:621px;width:168px}
.card-head{height:31px;border-radius:2px;background:linear-gradient(#6cb81f,#2f8a0c);color:#fff;font-size:12px;font-weight:700;text-transform:uppercase;display:flex;align-items:center;padding-left:19px;box-shadow:0 1px 2px rgba(0,0,0,.2)}
.card-photo{margin-top:9px;height:83px}
.card-text{margin-top:10px;font-size:8px;line-height:14px;color:#555}
.card .read-more{margin-top:14px}

.about-title{left:162px;top:880px}
.about-photo{left:161px;top:914px;width:162px;height:93px;background:linear-gradient(135deg,#d23a2e,#e9b88f 50%,#4a8fc4)}
.about-text{left:344px;top:912px;width:300px;line-height:16px;font-size:8.5px}
.about-text-full{left:161px;top:1018px;width:485px;line-height:16px;font-size:8.5px}
.about-btn{left:566px;top:1069px}

.events-title{left:666px;top:880px}
.event{left:668px;width:242px;display:flex;gap:15px}
.event-date{width:54px;height:54px;border-radius:50%;background:var(--grey-circle);color:#fff;display:flex;flex-direction:column;align-items:center;justify-content:center;flex:none}
.event-day{font-size:14px;line-height:14px}
.event-month{font-size:8px;font-weight:700;margin-top:3px}
.event-title{color:var(--green);font-size:8.5px;font-weight:700;text-transform:uppercase;margin-top:4px}
.event-text{font-size:8.5px;line-height:15px;margin-top:5px}
.event-rule{left:670px;top:982px;width:240px;height:1px;background:var(--line)}
.events-btn{left:829px;top:1068px}

.footer-rule{left:161px;top:1124px;width:749px;height:1px;background:var(--line)}
.footer-nav{left:161px;top:1141px;display:flex;font-size:8.5px;color:#444}
.footer-nav a{padding:0 20px;border-left:1px solid #444;line-height:10px}
.footer-nav a:first-child{border-left:none;padding-left:0}
.copyright{left:161px;top:1162px;font-size:8px;color:#444}
.social{left:778px;top:1145px;display:flex;gap:4px}
.social span{width:18px;height:18px;border-radius:50%;background:#ddd}
</style>
</head>
<body>

<div class="abs brand"><span class="brand-dot"></span>Maplecrest Kids Club</div>

<nav class="abs top-nav">
  <a href="#">Home</a><a href="#">Contact</a><a href="#">Locations</a><a href="#">Events</a><a href="#">About Us</a>
</nav>

<a class="abs btn newsletter" href="#">NEWSLETTER SIGNUP
  <svg width="11" height="9" viewBox="0 0 11 9"><path d="M1 1l3.5 3.5L1 8M6 1l3.5 3.5L6 8" fill="none" stroke="#fff" stroke-width="1.6"/></svg>
</a>

<nav class="abs main-nav">
  <a href="#">Programs</a><a href="#">Maplecrest Kids Club</a><a href="#">Tutions Express</a><a href="#">Party &amp; Rentals</a><a href="#">Kids Place</a><a href="#">Montessori</a><a href="#">Careers</a>
</nav>

<div class="abs hero" role="img" aria-label="Group of smiling children leaning in toward the camera"></div>
<div class="abs hero-shadow"></div>
<div class="abs caption caption-title">Maplecrest Kids Club</div>
<div class="abs caption caption-sub">Maplecrest Kids Club before and after school program exists</div>
<div class="abs slider-arrows"><span>‹</span><span>›</span></div>

<h2 class="abs welcome-title">Welcome to Maplecrest Kids Club</h2>
<p class="abs body-text welcome-text">Maplecrest Kids Club Before and After School Program exists to provide programming of the highest quality for your children, stressing a safe, secure environment; a nurturing, professional staff and lots of fun. We are committed to providing a fun-filled, rewarding program that supports the physical, mental, emotional and spiritual development of school-age children and their families to the fullest potential in order to improve their quality of life.</p>

<div class="abs card" style="left:161px">
  <div class="card-head">Programs</div>
  <div class="card-photo" role="img" aria-label="Children wrapped in colourful hooded towels" style="background:linear-gradient(90deg,#1d5fb8,#c8b32a 50%,#6b4fb0)"></div>
  <p class="card-text">Maplecrest Kids Club at the Birchwood Community Rec Center provides before &amp; after school programming of the highest quality, stressing a safe, secure environment...</p>
  <a class="btn read-more" href="#">Read more</a>
</div>
<div class="abs card" style="left:354px">
  <div class="card-head">Tutions Express</div>
  <div class="card-photo" role="img" aria-label="Children running across a green field" style="background:linear-gradient(#7fb33a,#4f9a22)"></div>
  <p class="card-text">Maplecrest Kids Club at the Birchwood Community Rec Center provides before &amp; after school programming of the highest quality, stressing a safe, secure environment...</p>
  <a class="btn read-more" href="#">Read more</a>
</div>
<div class="abs card" style="left:549px">
  <div class="card-head">Party &amp; Rentals</div>
  <div class="card-photo" role="img" aria-label="Children gathered around a birthday cake" style="background:linear-gradient(90deg,#c9423a,#e8c2a0 50%,#3f7fc0)"></div>
  <p class="card-text">Maplecrest Kids Club at the Birchwood Community Rec Center provides before &amp; after school programming of the highest quality, stressing a safe, secure environment...</p>
  <a class="btn read-more" href="#">Read more</a>
</div>
<div class="abs card" style="left:742px">
  <div class="card-head">Kids Place</div>
  <div class="card-photo" role="img" aria-label="Boys running along a sunny beach" style="background:linear-gradient(#8fc3e0,#d8e7ef 60%,#e8e4da)"></div>
  <p class="card-text">Maplecrest Kids Club at the Birchwood Community Rec Center provides before &amp; after school programming of the highest quality, stressing a safe, secure environment...</p>
  <a class="btn read-more" href="#">Read more</a>
</div>

<h2 class="abs about-title">About Maplecrest Kids Club</h2>
<div class="abs about-photo" role="img" aria-label="Children lying in a circle with heads together"></div>
<p class="abs about-text">Maplecrest Kids Club Before and After School Program exists to provide programming of the highest quality for your children, stressing a safe, secure environment; a nurturing, professional staff and lots of fun. We are committed to providing a fun-filled, rewarding program that supports the physical, mental, emotional and spiritual development of school-age children and their families to the fullest potential in order to improve their quality of life.</p>
<p class="abs about-text-full">Maplecrest Kids Club Before and After School Program exists to provide programming of the highest quality for your children, stressing a safe, secure environment; a nurturing, professional staff and lots of fun. Maplecrest Kids Club Before and After School Program exists to provide programming of the highest quality for your children.</p>
<a class="abs btn read-more about-btn" href="#">Read more</a>

<h2 class="abs events-title">Latest Events</h2>
<div class="abs event" style="top:915px">
  <div class="event-date"><span class="event-day">20</span><span class="event-month">AUG</span></div>
  <div><div class="event-title">Maplecrest before and after</div><p class="event-text">Maplecrest Kids Club Before and After School Program exists to provide...</p></div>
</div>
<div class="abs event-rule"></div>
<div class="abs event" style="top:993px">
  <div class="event-date"><span class="event-day">27</span><span class="event-month">AUG</span></div>
  <div><div class="event-title">Maplecrest before and after</div><p class="event-text">Maplecrest Kids Club Before and After School Program exists to provide...</p></div>
</div>
<a class="abs btn read-more events-btn" href="#">Read more</a>

<div class="abs footer-rule"></div>
<nav class="abs footer-nav">
  <a href="#">Home</a><a href="#">Contact</a><a href="#">Locations</a><a href="#">Events</a><a href="#">About Us</a>
</nav>
<p class="abs copyright">Copyright © 2013. Maplecrest Kids Club. All Rights Reserved.</p>
<div class="abs social" aria-label="Social links"><span></span><span></span><span></span><span></span><span></span><span></span></div>

</body>
</html>
```